Webdesign für Brenner Flusskraft
Zielgruppe
Ansprechpartner für Planung und Errichtung von Stromerzeugung durch erneuerbare Energien. Alle Interessen im privaten, teilöffentlichen und öffentlichen Bereich, die mittel- und langfristig umweltschonenden Strom nutzen wollen.
Aufgabenstellung
- Farben bitte in den Unternehmensfarben Blau/Weiß mit einem kleinen Anteil Orange
- Bilder nach Möglichkeit bitte nur eigene (siehe Anhang)
- klare und übersichtliche Struktur
- KEIN Abklatsch der alten Webseite

```html
<!DOCTYPE html>
<html lang="de">
<head>
<meta charset="utf-8">
<title>Brenner Flusskraft</title>
<link href="https://fonts.googleapis.com/css2?family=Lato:wght@400;700;900&family=Rubik:wght@400;500&family=Poppins:wght@300;400;500;700&family=Arimo:wght@400;700&display=swap" rel="stylesheet">
<style>
:root{
  --navy:#00008c;
  --white:#ffffff;
  --paper:#f7f7f7;
  --grey:#d6d6d6;
  --footer:#d9d9d9;
  --ink:#111111;
  --muted:#8a8a8a;
  --brown:#8b3b2a;
  --orange:#ff8a1c;
  --sky:#5fa8ff;
}
*{margin:0;padding:0;box-sizing:border-box}
html,body{width:1200px;height:3737px;overflow:hidden}
body{position:relative;background:var(--white);font-family:'Arimo',Arial,sans-serif;color:var(--ink)}
.abs{position:absolute}
.nav{left:0;top:0;width:1200px;height:51px;background:var(--navy)}
.nav a{position:absolute;top:12px;color:var(--white);font:500 15px 'Rubik',sans-serif;text-decoration:none;white-space:nowrap}
.hero{left:0;top:51px;width:1200px;height:660px;background:var(--paper)}
.brand-badge{left:0;top:29px;width:160px;height:160px;border-radius:50%;background:var(--white);display:flex;align-items:center;justify-content:center;text-align:center;color:var(--navy);font:900 19px/1.1 'Lato',sans-serif}
.hero-title{left:682px;top:140px;color:var(--brown);font:900 35px/1.12 'Lato',sans-serif;white-space:nowrap}
.hero-text{left:590px;top:292px;width:505px;text-align:center;font-size:16.5px;line-height:19.5px}
.tiles{left:705px;top:540px;display:flex;gap:2px}
.tile{width:104px;height:72px;background:var(--navy);display:flex;flex-direction:column;align-items:center;justify-content:flex-end;padding-bottom:6px;color:var(--white);font:900 10px 'Lato',sans-serif;white-space:nowrap}
.tile span{color:var(--orange)}
.tile svg{margin-bottom:5px}
.mission-title{left:112px;top:794px;display:flex;align-items:center;gap:8px;color:var(--navy);font:900 34px 'Lato',sans-serif;white-space:nowrap}
.sector-panel{left:0;top:900px;width:273px;height:258px;background:var(--grey);border-bottom-left-radius:116px}
.sector-list{left:81px;top:923px;width:158px;list-style:none;font-size:17px}
.sector-list li{border-bottom:1px solid var(--ink);padding:2px 0 3px;margin-bottom:7px;white-space:nowrap}
.why-title{left:325px;top:919px;width:250px;text-align:center;font:700 15px 'Arimo',sans-serif}
.why-text{left:325px;top:961px;width:290px;font-size:12px;line-height:14.5px}
.btn{border:1.5px solid var(--navy);border-radius:16px;background:var(--white);color:var(--ink);font-size:13px;text-align:center;line-height:24px;white-space:nowrap}
.btn-light{border:1.5px solid var(--white);background:transparent;color:var(--white);font-size:13px;line-height:23px;letter-spacing:-0.1px}
.partner-img{left:682px;top:846px;width:435px;height:253px;background:linear-gradient(135deg,#6f9a58 0%,#c7b690 45%,#e9e2d2 70%,#cfcfd6 100%);border:1px solid #e5e5e5}
.partner-caption{left:700px;top:1099px;width:412px;text-align:right;font-size:16px;white-space:nowrap}
.partner-caption b{color:var(--navy);font:900 19px 'Lato',sans-serif}
.section-title{left:0;top:1194px;width:1200px;text-align:center;font:900 33px 'Lato',sans-serif}
.card{background:var(--navy);color:var(--white)}
.card h3{position:absolute;display:flex;align-items:center;gap:14px;font:900 35px 'Lato',sans-serif;white-space:nowrap}
.card .rule{position:absolute;height:3px;background:var(--white)}
.card p{position:absolute;font-size:14.5px;line-height:16px}
.banner{left:0;top:1797px;width:1200px;height:213px;background:linear-gradient(180deg,#b9bcd0 0%,#9aa0c4 40%,#5863c8 75%,#2b34c7 100%)}
.banner-rule{left:83px;top:1862px;width:1034px;height:1px;background:var(--ink)}
.banner-label{top:1868px;font:900 16px 'Lato',sans-serif;color:#131313;white-space:nowrap}
.rating{left:498px;top:1942px;display:flex;align-items:center;gap:6px;white-space:nowrap}
.avatar{width:22px;height:22px;border-radius:50%;background:#8d8d9a;border:2px solid var(--white)}
.rating small{display:block;font:700 8px 'Arimo',sans-serif;color:#1b1b4f}
.projects-title{left:73px;top:2095px;font:500 37px/44px 'Rubik',sans-serif}
.projects-rule{left:73px;top:2193px;width:58px;height:2px;background:var(--navy)}
.project{width:334px}
.project .photo{height:236px;position:relative}
.project .tag{position:absolute;left:198px;top:17px;width:118px;height:22px;background:var(--white);text-align:center;font:500 13px/22px 'Rubik',sans-serif}
.project .meta{margin:26px 0 0 37px;font:400 15px 'Rubik',sans-serif;white-space:nowrap}
.project .meta span{color:var(--muted);border-left:1px solid #ccc;padding-left:14px;margin-left:14px}
.project h4{margin:34px 0 0 37px;font:500 22px 'Rubik',sans-serif;white-space:nowrap}
.project p{margin:35px 0 0 37px;width:250px;color:var(--muted);font:400 13.5px/18px 'Rubik',sans-serif}
.project hr{border:0;border-top:1px solid #e6e6e6;margin-top:34px}
.project .more{margin:28px 0 0 37px;font:400 15px 'Rubik',sans-serif;display:flex;align-items:center;gap:8px}
.cta{left:0;top:2890px;width:1200px;height:527px;background:var(--navy)}
.cta-kicker{left:142px;top:2970px;color:var(--sky);font:700 9px 'Poppins',sans-serif;letter-spacing:4px;white-space:nowrap}
.cta-title{left:142px;top:2985px;color:var(--white);font:300 45px/51px 'Poppins',sans-serif;white-space:nowrap}
.cta-text{left:142px;top:3165px;width:360px;color:var(--white);font:400 12px/20px 'Poppins',sans-serif}
.cta-list{left:142px;top:3255px;list-style:none;color:var(--white);font:400 12px 'Poppins',sans-serif;white-space:nowrap}
.cta-list li{display:flex;align-items:center;gap:12px;height:26px}
.footer{left:0;top:3417px;width:1200px;height:264px;background:var(--footer)}
.footer-badge{left:148px;top:3440px;width:116px;height:116px;border-radius:50%;background:var(--white);display:flex;align-items:center;justify-content:center;text-align:center;color:var(--navy);font:900 16px/1.1 'Lato',sans-serif}
.footer-about{left:93px;top:3549px;width:260px;font:400 12px/18px 'Poppins',sans-serif}
.footer-col{top:3480px;font:400 13px 'Poppins',sans-serif;white-space:nowrap}
.footer-col h5{font:500 16px 'Poppins',sans-serif;margin-bottom:14px}
.footer-col ul{list-style:none}
.footer-col li{position:relative;padding-left:22px;height:27.5px}
.footer-col li::before{content:"";position:absolute;left:0;top:5px;width:8px;height:8px;border-radius:50%;background:var(--navy)}
.bottom-bar{left:0;top:3681px;width:1200px;height:56px;background:var(--navy);color:var(--white);text-align:center;font:400 13px/56px 'Poppins',sans-serif}
</style>
</head>
<body>

<nav class="abs nav">
  <a style="left:527px">Start</a>
  <a style="left:632px">Über uns</a>
  <a style="left:718px">Services ▾</a>
  <a style="left:822px">Seite ▾</a>
  <a style="left:902px">Kontakt</a>
</nav>

<section class="abs hero">
  <svg class="abs" style="left:0;top:0" width="624" height="660">
    <defs><linearGradient id="heroPhoto" x1="0" y1="0" x2="1" y2="1"><stop offset="0" stop-color="#2d3b24"/><stop offset="0.5" stop-color="#4e6a39"/><stop offset="1" stop-color="#1e2619"/></linearGradient></defs>
    <polygon points="0,0 392,0 624,660 0,660" fill="url(#heroPhoto)" role="img" aria-label="Foto der Inhaberfamilie, zwei Männer in hellblauen Hemden vor grünen Bäumen"/>
  </svg>
  <div class="abs brand-badge">Brenner<br>Flusskraft</div>
  <h1 class="abs hero-title">HERZLICHST IHRE<br>FAMILIE BRENNER!</h1>
  <p class="abs hero-text">Willkommen auf unserer Website, wo wir Ihnen Lösungen im Bereich erneuerbare Energien vorstellen. Unsere Expertise erstreckt sich auf Solarenergie, Windenergie und Wasserkraft - die Eckpfeiler einer nachhaltigen Zukunft.</p>
  <div class="abs tiles">
    <div class="tile"><svg width="30" height="30" viewBox="0 0 30 30"><path d="M12 3 C6 12 4 16 4 19 a8 8 0 0 0 16 0 C20 16 18 12 12 3Z" fill="#fff"/><path d="M22 9 l-4 8 h4 l-3 8 7-10 h-4 l3-6z" fill="#fff"/></svg><div>WASSER <span>KRAFT</span></div></div>
    <div class="tile"><svg width="44" height="28" viewBox="0 0 44 28"><circle cx="22" cy="6" r="4" fill="#fff"/><path d="M6 22 L10 12 H34 L38 22Z" fill="#fff"/><path d="M14 12 L12 22 M22 12 V22 M30 12 L32 22 M8 17 H36" stroke="#00008c" stroke-width="1.5"/><rect x="21" y="22" width="2" height="5" fill="#fff"/></svg><div>PHOTO<span>VOLTAIK</span></div></div>
    <div class="tile" style="width:114px"><svg width="44" height="30" viewBox="0 0 44 30"><path d="M4 22 V17 l6-6 h16 l6 6 h4 v5Z" fill="#fff"/><circle cx="12" cy="23" r="4" fill="#00008c" stroke="#fff" stroke-width="2"/><circle cx="30" cy="23" r="4" fill="#00008c" stroke="#fff" stroke-width="2"/><path d="M36 2 v5 M40 2 v5 M34 7 h8 v4 a4 4 0 0 1-8 0Z M38 15 v4" stroke="#fff" stroke-width="2" fill="none"/></svg><div>ELECTRO<span>MOBILITY</span></div></div>
  </div>
</section>

<h2 class="abs mission-title"><svg width="46" height="52" viewBox="0 0 46 52"><path d="M8 48 V20 M22 48 V12 M36 48 V20" stroke="#00008c" stroke-width="2.5"/><path d="M8 20 l-6-6 M8 20 l8-3 M8 20 l-2 8 M22 12 l-7-6 M22 12 l9-3 M22 12 l-2 9 M36 20 l-6-6 M36 20 l8-3 M36 20 l-2 8" stroke="#00008c" stroke-width="2"/><path d="M2 50 H44" stroke="#5a5ad0" stroke-width="2"/></svg>UNSERE MISSION</h2>

<div class="abs sector-panel"></div>
<ul class="abs sector-list">
  <li>Industrielle Prozesse</li>
  <li>Telekommunikation</li>
  <li>Verkehrssysteme</li>
  <li>Gesundheitswesen</li>
</ul>
<h3 class="abs why-title">WARUM WIR</h3>
<p class="abs why-text">Wir setzen uns leidenschaftlich für den Übergang zu erneuerbaren Energien ein. Unsere Mission ist es, saubere und nachhaltige Energielösungen für Privathaushalte und Unternehmen anzubieten, um unsere Umwelt zu schützen und Geld zu sparen.</p>
<div class="abs btn" style="left:416px;top:1064px;width:99px;height:27px">KONTAKT</div>
<div class="abs partner-img" role="img" aria-label="Foto ausgelegter Prospekte zur Partnerschaft im Bereich Solarenergie"></div>
<p class="abs partner-caption">im Partnerschat mit <b>Solvana</b></p>

<h2 class="abs section-title">LEISTUNGEN</h2>

<article class="abs card" style="left:78px;top:1262px;width:513px;height:535px;border-top-left-radius:87px">
  <h3 style="left:43px;top:40px"><svg width="52" height="40" viewBox="0 0 30 26"><path d="M10 2 C5 10 3 14 3 17 a7 7 0 0 0 14 0 C17 14 15 10 10 2Z" fill="#fff"/><path d="M21 6 l-4 8 h4 l-3 8 7-10 h-4 l3-6z" fill="#fff"/></svg>WASSER</h3>
  <div class="rule" style="left:38px;top:83px;width:264px"></div>
  <p style="left:44px;top:179px;width:440px;font-size:16.5px;line-height:19.3px">Als Betreiber von Wasserkraftanlagen lassen wir eigene wertvollen Erfahrungen in unsere Projekte einfließen und stehen Ihnen immer als kompetenter Ansprechpartner in allen Fragen rund um die Wasserkraft zur Verfügung.<br>Mit unseren modularen Steuerungen können wir in kurzer Zeit auf Ihre Wünsche Reagieren und halten gleichzeitig Ausfallkosten und Wartungsaufwand minimal.</p>
  <div class="abs btn btn-light" style="left:179px;top:392px;width:123px;height:26px">MEHR ERFAHREN</div>
</article>

<article class="abs card" style="left:602px;top:1262px;width:515px;height:265px">
  <h3 style="left:16px;top:36px"><svg width="56" height="40" viewBox="0 0 44 28"><circle cx="24" cy="6" r="4" fill="#fff"/><path d="M4 24 L9 12 H35 L40 24Z" fill="#fff"/><path d="M15 12 L13 24 M22 12 V24 M29 12 L31 24 M7 18 H38" stroke="#00008c" stroke-width="1.5"/></svg>SOLAR</h3>
  <div class="rule" style="left:18px;top:83px;width:258px"></div>
  <p style="left:26px;top:124px;width:460px">Als Experten im Bereich regenerative Energien finden Sie mit uns Ihren Partner zur Verwirklichung Ihrer Potovoltaikprojekte. Von der Errichtung eines Solarparks im Megawattbereich bis zur autarken Insellösung im Eigenheim stehen wir Ihnen mit unserem Expertenwissen zur Seite.<br>Wir helfen Ihnen den Eigenverbrauch Ihrer PV-Anlage zu steigern.</p>
  <div class="abs btn btn-light" style="left:164px;top:219px;width:123px;height:26px">MEHR ERFAHREN</div>
</article>

<article class="abs card" style="left:601px;top:1538px;width:516px;height:259px">
  <h3 style="left:17px;top:22px"><svg width="56" height="42" viewBox="0 0 44 30"><path d="M4 24 V18 l6-6 h16 l6 6 h4 v6Z" fill="#fff"/><circle cx="12" cy="24" r="4" fill="#00008c" stroke="#fff" stroke-width="2"/><circle cx="30" cy="24" r="4" fill="#00008c" stroke="#fff" stroke-width="2"/><path d="M36 1 v5 M40 1 v5 M34 6 h8 v4 a4 4 0 0 1-8 0Z M38 14 v4" stroke="#fff" stroke-width="2" fill="none"/></svg>ELECTRO</h3>
  <div class="rule" style="left:18px;top:66px;width:264px"></div>
  <p style="left:27px;top:97px;width:460px">ist zum Tagesgespräch geworden. Wir sprechen nicht nur darüber, wir gestalten die Elektromobilität.<br>Wir sind Ihr Mobilitätsdienstleister und begleiten Sie auf neuen Wegen. Ob eine Testfahrt in einem Elektrofahrzeug, die Langzeitmiete oder das Errichten eines Elektroladeparkplatzes - bei uns sind Sie richtig aufgehoben.</p>
  <div class="abs btn btn-light" style="left:165px;top:207px;width:123px;height:26px">MEHR ERFAHREN</div>
</article>

<div class="abs banner" role="img" aria-label="Luftbild einer Solaranlage unter bewölktem Himmel"></div>
<div class="abs banner-rule"></div>
<span class="abs banner-label" style="left:83px">FACHKENNTNISSE &amp; ERFAHRUNG</span>
<span class="abs banner-label" style="left:447px">KUNDENSPEZIFISCHE LÖSUNGEN</span>
<span class="abs banner-label" style="left:768px">QUALITÄTSPRODUKTE &amp; DIENSTLEISTUNGEN</span>
<div class="abs rating">
  <div style="display:flex"><div class="avatar"></div><div class="avatar" style="margin-left:-8px;background:#6a6a7a"></div></div>
  <div>
    <div style="font:700 12px 'Arimo',sans-serif;color:#1b1b4f">4.9 <span style="color:#ffc21c;letter-spacing:2px">★★★★★</span></div>
    <small>Rating reviews 12K+ people</small>
  </div>
</div>

<h2 class="abs projects-title">Letzte Projekte &amp;<br>Updates</h2>
<div class="abs projects-rule"></div>

<article class="abs project" style="left:73px;top:2231px">
  <div class="photo" style="background:linear-gradient(180deg,#9fb8c8 0%,#7f9486 45%,#b4bcc4 70%,#d9dde3 100%)" role="img" aria-label="Foto einer Solardachanlage mit Monteur"><div class="tag">Solar</div></div>
  <div class="meta">September 23<span>Dortmund</span></div>
  <h4>Solarzellenkomponenten</h4>
  <p>Magna aliqua umt enimd mini venia quis ulamco aliquip commodo cons equat duis aute irue derit...</p>
  <hr>
  <div class="more">mehr lesen <svg width="20" height="10" viewBox="0 0 20 10"><path d="M0 5 H16 M12 1 L17 5 L12 9" stroke="#00008c" stroke-width="2" fill="none"/></svg></div>
</article>

<article class="abs project" style="left:438px;top:2231px">
  <div class="photo" style="background:linear-gradient(180deg,#cfd4d6 0%,#8a9078 45%,#9c978f 75%,#7f7a74 100%)" role="img" aria-label="Foto einer Ladesäule für Elektroautos auf einem Parkplatz"><div class="tag">electro</div></div>
  <div class="meta">September 23<span>Düsseldorf</span></div>
  <h4>Generatorkomponenten</h4>
  <p>Magna aliqua umt enimd mini venia quis ulamco aliquip commodo cons equat duis aute irue derit...</p>
  <hr>
  <div class="more">mehr lesen <svg width="20" height="10" viewBox="0 0 20 10"><path d="M0 5 H16 M12 1 L17 5 L12 9" stroke="#00008c" stroke-width="2" fill="none"/></svg></div>
</article>

<article class="abs project" style="left:802px;top:2231px">
  <div class="photo" style="background:linear-gradient(180deg,#3d4a5e 0%,#c9793a 45%,#6b4a30 70%,#2a2f3a 100%)" role="img" aria-label="Foto eines Technikers zwischen Solarmodulen im Sonnenuntergang"><div class="tag">solar</div></div>
  <div class="meta">September 23<span>Berlin</span></div>
  <h4>Photovoltaikanlage</h4>
  <p>Magna aliqua umt enimd mini venia quis ulamco aliquip commodo cons equat duis aute irue derit...</p>
  <hr>
  <div class="more">mehr lesen <svg width="20" height="10" viewBox="0 0 20 10"><path d="M0 5 H16 M12 1 L17 5 L12 9" stroke="#00008c" stroke-width="2" fill="none"/></svg></div>
</article>

<section class="abs cta">
  <svg class="abs" style="left:537px;top:0" width="663" height="527">
    <defs><linearGradient id="ctaPhoto" x1="0" y1="0" x2="1" y2="1"><stop offset="0" stop-color="#6f8fbf"/><stop offset="0.45" stop-color="#d9632a"/><stop offset="1" stop-color="#2b3f6e"/></linearGradient></defs>
    <polygon points="0,0 663,0 663,527 80,527" fill="url(#ctaPhoto)" role="img" aria-label="Foto von Monteuren mit Schutzhelmen bei der Installation von Solarmodulen"/>
  </svg>
</section>
<p class="abs cta-kicker">FÜR SAUBERE ENERGIE</p>
<h2 class="abs cta-title">Ihr Partner für<br>saubere<br>Energie!</h2>
<p class="abs cta-text">Als Familienunternehmen in zweiter Generation finden Sie bei uns kurze Wege, hohe qualitative Leistungen und einen großenErfahrungsschatz.</p>
<ul class="abs cta-list">
  <li><svg width="12" height="10" viewBox="0 0 12 10"><path d="M1 5 L4.5 8.5 L11 1.5" stroke="#fff" stroke-width="2" fill="none"/></svg>Umfassende Fachkenntnisse und Erfahrung</li>
  <li><svg width="12" height="10" viewBox="0 0 12 10"><path d="M1 5 L4.5 8.5 L11 1.5" stroke="#fff" stroke-width="2" fill="none"/></svg>Umweltfreundlichkeit und Nachhaltigkeit.</li>
  <li><svg width="12" height="10" viewBox="0 0 12 10"><path d="M1 5 L4.5 8.5 L11 1.5" stroke="#fff" stroke-width="2" fill="none"/></svg>kostenlose beratung.</li>
</ul>

<footer class="abs footer"></footer>
<div class="abs footer-badge">Brenner<br>Flusskraft</div>
<p class="abs footer-about">Lorem ipsum dolor sit amet, consectetur adipiscing elit. Ut elit tellus, luctus nec ullamcorper mattis, pulvinar dapibus leo.</p>
<div class="abs footer-col" style="left:454px">
  <h5>Kontakt</h5>
  <ul>
    <li>Brenner - Energietechnik</li>
    <li>09999 Auenfeld</li>
    <li>Telefon:035550199</li>
    <li style="line-height:18px">info@energietechnik-<br>brenner.de</li>
  </ul>
</div>
<div class="abs footer-col" style="left:726px">
  <h5>Rechtliches</h5>
  <ul><li>Datenschutz</li><li>Impressum</li><li>AGB</li><li>Index2</li></ul>
</div>
<div class="abs footer-col" style="left:997px">
  <h5>Social Media</h5>
  <ul><li>Freundebuch</li><li>Bilderstrom</li><li>Pinnwand</li><li>Berufsnetz</li></ul>
</div>
<div class="abs bottom-bar">Copyright 2023 © &nbsp;| Powered by mir</div>

</body>
</html>
```